Aerospace Center needs app design

We need a design that would be a creative and innovative look of a simple idea connecting air traffic control situations with sonification.
We would like to see designs that use the elements shown in the short video which are different pads, showing 4 different colors, connecting with a degree and feeling of urgency. The different pads will be movable over screen, similar as to a whiteboard where you can move things around. Each of those pads has 4 different elements that are shown:
- ATC Event (you can chose different setups)
- Select a status (you can chose between Information, Caution and Alert. Color needs to feel more alert from Information to Alert.
- Notes box (you can open the box and write additional text on it)
- Music (you can chose different files. on the right side you can see a small group of notes. When you hover over the notes, music will be played without pressing a play or stop button.
The second video is an overview of music archival program that is connected with the pads.
Look and feel
Each slider illustrates characteristics of the customer's brand and the style your logo design should communicate.

```html
<!DOCTYPE html>
<html lang="en">
<head>
<meta charset="utf-8">
<title>AVIX – Sonification Pads</title>
<link rel="stylesheet" href="https://fonts.googleapis.com/css2?family=Montserrat:wght@400;500;600;700;800&display=swap">
<style>
:root{
  --navy:#021824;
  --orange:#ff6a00;
  --page:#f7efea;
  --white:#ffffff;
  --text:#3a3a3a;
  --idle-head:#b8c7f3;
  --idle-border:#dfe3ee;
  --field-border:#d8d8d8;
}
*{box-sizing:border-box;margin:0;padding:0}
html,body{width:1200px;height:803px;overflow:hidden}
body{font-family:'Montserrat',sans-serif;background:var(--page);position:relative;color:var(--text)}

.sidebar{position:absolute;left:0;top:0;width:145px;height:803px;background:var(--navy)}
.nav-item{position:absolute;left:0;width:145px;height:76px;display:flex;align-items:center;color:var(--white);font-size:14px;font-weight:500}
.nav-item svg{position:absolute;left:28px;width:17px;height:17px;fill:var(--white)}
.nav-item span{position:absolute;left:64px}
.nav-item.active{background:var(--orange);height:98px;top:0}
.nav-divider{position:absolute;left:11px;width:124px;height:1px;background:#22343f}

.topbar{position:absolute;left:145px;top:0;width:1055px;height:98px;background:var(--navy)}
.brand{position:absolute;left:80px;top:29px;color:var(--white);font-weight:800;font-size:36px;letter-spacing:1px}
.zoom{position:absolute;left:299px;top:28px;width:113px;height:44px;border:2px solid var(--white);border-radius:22px}
.zoom svg{position:absolute;left:20px;top:8px}
.search{position:absolute;left:420px;top:27px;width:346px;height:44px;border-radius:22px;background:var(--white);padding-left:28px;line-height:44px;font-size:14px;color:#777}
.welcome{position:absolute;right:166px;top:22px;text-align:right;color:var(--white)}
.welcome small{display:block;font-size:13px;font-weight:500}
.welcome strong{display:block;font-size:18px;font-weight:700;margin-top:2px}
.avatar{position:absolute;left:900px;top:16px;width:50px;height:50px;border-radius:50%;background:radial-gradient(circle at 50% 40%,#c99a7d,#5b4a3f 70%)}
.logout{position:absolute;left:1009px;top:29px}

.board{position:absolute;left:164px;top:118px;width:1018px;height:608px;background:var(--white);border-radius:6px;border:1px solid #eee}

.pad{position:absolute;width:190px;height:278px;border:2px solid var(--idle-border);background:linear-gradient(160deg,#eef1fb,#e9e6ef 60%,#efe8ee)}
.pad-head{position:absolute;left:8px;top:7px;width:174px;height:35px;border-radius:3px;background:var(--idle-head);color:var(--white);font-weight:700;font-size:16px;line-height:35px;padding-left:18px}
.pad-head .close{position:absolute;right:13px;top:10px;width:15px;height:15px;border-radius:50%;background:var(--white)}
.pad-head .close::before,.pad-head .close::after{content:"";position:absolute;left:7px;top:3.5px;width:1.6px;height:8px;background:var(--idle-head);transform:rotate(45deg)}
.pad-head .close::after{transform:rotate(-45deg)}
.field{position:absolute;left:10px;width:168px;height:38px;background:var(--white);border:1px solid var(--field-border);font-size:11.5px;line-height:36px;padding-left:16px;color:var(--text)}
.field.select::after{content:"";position:absolute;right:16px;top:16px;border-left:4px solid transparent;border-right:4px solid transparent;border-top:5px solid #444}
.field.notes{width:120px}
.f1{top:50px}.f2{top:98px}.f3{top:146px}.f4{top:194px}
.music{position:absolute;left:150px;top:244px}

.pad.p1{border-color:#ff6a1a;background:linear-gradient(45deg,#ff3d14 0%,#ff8a14 40%,#fbe51e 100%)}
.pad.p1 .pad-head{background:#ff5a12}.pad.p1 .close::before,.pad.p1 .close::after{background:#ff5a12}
.pad.p2{border-color:#16d8f2;background:linear-gradient(45deg,#0ef2fa 0%,#3cc0f6 50%,#57a2f3 100%)}
.pad.p2 .pad-head{background:#4aa8f6}.pad.p2 .close::before,.pad.p2 .close::after{background:#4aa8f6}
.pad.p3{border-color:#8b3df0;background:linear-gradient(45deg,#6524e8 0%,#8a4ee4 40%,#e3b8d6 100%)}
.pad.p3 .pad-head{background:#7a34e6}.pad.p3 .close::before,.pad.p3 .close::after{background:#7a34e6}
.pad.p4{border-color:#f3b0b8;background:linear-gradient(45deg,#fbd6ef 0%,#f8a7b0 60%,#f27a7a 100%)}
.pad.p4 .pad-head{background:#f28080}.pad.p4 .close::before,.pad.p4 .close::after{background:#f28080}

.footer{position:absolute;left:0;width:1200px;top:763px;padding-left:145px;text-align:center;font-size:14px;color:#222;padding-left:145px}
.footer .sep{margin:0 6px}
</style>
</head>
<body>
<svg width="0" height="0" style="position:absolute">
  <defs>
    <symbol id="notes" viewBox="0 0 24 24">
      <g fill="none" stroke="#111" stroke-width="1.6">
        <path d="M6 20V7l5-2M13 18V5l7-2v13M13 8l7-2"/>
        <ellipse cx="4.3" cy="20" rx="2" ry="1.6"/>
        <ellipse cx="11.3" cy="18" rx="2" ry="1.6"/>
        <ellipse cx="18.3" cy="16" rx="2" ry="1.6"/>
      </g>
    </symbol>
  </defs>
</svg>

<nav class="sidebar">
  <div class="nav-item active"><svg viewBox="0 0 20 20"><path d="M10 2 1 10h3v8h4v-5h4v5h4v-8h3z"/></svg><span>Home</span></div>
  <div class="nav-item" style="top:91px"><svg viewBox="0 0 20 20"><path d="M2 4h16v14H2zM5 1h2v4H5zm8 0h2v4h-2zM4 8h12v8H4z" fill-rule="evenodd"/></svg><span>Orders</span></div>
  <div class="nav-divider" style="top:164px"></div>
  <div class="nav-item" style="top:167px"><svg viewBox="0 0 20 20"><circle cx="10" cy="6" r="3"/><circle cx="4" cy="7" r="2.2"/><circle cx="16" cy="7" r="2.2"/><path d="M5 17c0-4 2-6 5-6s5 2 5 6zM0 15c0-3 1.5-4.5 4-4.5l1 .3C4 12 3.5 13.5 3.5 15zM20 15c0-3-1.5-4.5-4-4.5l-1 .3c1 1.2 1.5 2.7 1.5 4.2z"/></svg><span>Analytics</span></div>
  <div class="nav-divider" style="top:244px"></div>
  <div class="nav-item" style="top:243px"><svg viewBox="0 0 20 20"><path d="M10 3a7 7 0 1 1-6.6 9.3l2.3-.8A4.6 4.6 0 1 0 6.6 6.7L9 9H2V2l2.9 2.9A7 7 0 0 1 10 3z"/></svg><span>Catgories</span></div>
  <div class="nav-item" style="top:319px"><svg viewBox="0 0 20 20"><path d="M1 4h18v12H1zm2 2v2h14V6zm0 5v3h14v-3zm1 1h4v1H4z" fill-rule="evenodd"/></svg><span>Collections</span></div>
  <div class="nav-divider" style="top:397px"></div>
  <div class="nav-item" style="top:395px"><svg viewBox="0 0 20 20"><path d="M4 1h8l5 5v13H4zm2 2v14h9V7h-4V3zm1 7h7v1.5H7zm0 3h7v1.5H7z" fill-rule="evenodd"/></svg><span>Offers</span></div>
  <div class="nav-divider" style="top:469px"></div>
  <div class="nav-item" style="top:471px"><svg viewBox="0 0 20 20"><path d="M1 2h2v14h16v2H1zm4 11 4-5 3 3 5-6 1.5 1.2-6.4 7.7-3-3-2.6 3.3z"/></svg><span>Employess</span></div>
</nav>

<header class="topbar">
  <div class="brand">AVIX</div>
  <div class="zoom">
    <svg width="70" height="26" viewBox="0 0 70 26" fill="none" stroke="#fff" stroke-width="2.2">
      <circle cx="11" cy="10" r="8"/><path d="M17 16l6 6M7 10h8M11 6v8"/>
      <circle cx="39" cy="10" r="8"/><path d="M45 16l6 6M35 10h8"/>
    </svg>
  </div>
  <div class="search">Search</div>
  <div class="welcome"><small>Welcome</small><strong>John Doe</strong></div>
  <div class="avatar" role="img" aria-label="User profile photo"></div>
  <svg class="logout" width="30" height="26" viewBox="0 0 30 26"><path d="M3 3h9v3H6v14h6v3H3z" fill="#fff"/><path d="M12 9h7V3l10 10-10 10v-6h-7z" fill="#fff"/></svg>
</header>

<main class="board"></main>

<!-- Row 1 -->
<section class="pad p1" style="left:181px;top:139px">
  <div class="pad-head">SO 1<span class="close"></span></div>
  <div class="field select f1">Select atc event</div>
  <div class="field select f2">1.Information</div>
  <div class="field notes f3">Notes</div>
  <div class="field select f4">Holt T..</div>
  <svg class="music" width="24" height="24"><use href="#notes"/></svg>
</section>
<section class="pad p2" style="left:379px;top:139px">
  <div class="pad-head">SO 2<span class="close"></span></div>
  <div class="field select f1">Landing</div>
  <div class="field select f2">1.Information</div>
  <div class="field notes f3">Notes</div>
  <div class="field select f4">Holt T..</div>
  <svg class="music" width="24" height="24"><use href="#notes"/></svg>
</section>
<section class="pad p3" style="left:578px;top:139px">
  <div class="pad-head">SO 3<span class="close"></span></div>
  <div class="field select f1">Departure</div>
  <div class="field select f2">2.Caution</div>
  <div class="field notes f3">Notes</div>
  <div class="field select f4">Verano..</div>
  <svg class="music" width="24" height="24"><use href="#notes"/></svg>
</section>
<section class="pad p4" style="left:777px;top:139px">
  <div class="pad-head">SO 4<span class="close"></span></div>
  <div class="field select f1">Moon</div>
  <div class="field select f2">3.Alert</div>
  <div class="field notes f3">Notes</div>
  <div class="field select f4">Holt T..</div>
  <svg class="music" width="24" height="24"><use href="#notes"/></svg>
</section>
<section class="pad" style="left:975px;top:139px">
  <div class="pad-head">SO 5<span class="close"></span></div>
  <div class="field select f1">Select atc event</div>
  <div class="field select f2">Select Status..</div>
  <div class="field notes f3">Notes</div>
  <div class="field select f4">Select..</div>
  <svg class="music" width="24" height="24"><use href="#notes"/></svg>
</section>

<!-- Row 2 -->
<section class="pad" style="left:181px;top:426px">
  <div class="pad-head">SO 6<span class="close"></span></div>
  <div class="field select f1">Select atc event</div>
  <div class="field select f2">Select Status..</div>
  <div class="field notes f3">Notes</div>
  <div class="field select f4">Select..</div>
  <svg class="music" width="24" height="24"><use href="#notes"/></svg>
</section>
<section class="pad" style="left:379px;top:426px">
  <div class="pad-head">SO 7<span class="close"></span></div>
  <div class="field select f1">Select atc event</div>
  <div class="field select f2">Select Status..</div>
  <div class="field notes f3">Notes</div>
  <div class="field select f4">Select..</div>
  <svg class="music" width="24" height="24"><use href="#notes"/></svg>
</section>
<section class="pad" style="left:578px;top:426px">
  <div class="pad-head">SO 8<span class="close"></span></div>
  <div class="field select f1">Select atc event</div>
  <div class="field select f2">Select Status..</div>
  <div class="field notes f3">Notes</div>
  <div class="field select f4">Select..</div>
  <svg class="music" width="24" height="24"><use href="#notes"/></svg>
</section>
<section class="pad" style="left:777px;top:426px">
  <div class="pad-head">SO 9<span class="close"></span></div>
  <div class="field select f1">Select atc event</div>
  <div class="field select f2">Select Status..</div>
  <div class="field notes f3">Notes</div>
  <div class="field select f4">Select..</div>
  <svg class="music" width="24" height="24"><use href="#notes"/></svg>
</section>
<section class="pad" style="left:975px;top:426px">
  <div class="pad-head">SO 10<span class="close"></span></div>
  <div class="field select f1">Select atc event</div>
  <div class="field select f2">Select Status..</div>
  <div class="field notes f3">Notes</div>
  <div class="field select f4">Select..</div>
  <svg class="music" width="24" height="24"><use href="#notes"/></svg>
</section>

<footer class="footer">(c)2021 Companyname.All Rights Reserved<span class="sep">|</span>Privacy Policy<span class="sep">|</span>Terms and Use</footer>
</body>
</html>
```